Home Remodeling company needs a business card design

we need a business card design for home remodeling company in hamilton county, indiana USA. we offers a wide range of construction services including whole house renovations, Design and Build Basements and Kitchen and Bathroom Remodeling . we would like to see designs for both site of business card that use the same color of the company logo and also including all information below :
1- Karim Feltous CEO / General Contractor
2- all company contacts Telephone numbers ( 1-888-DULOM-47 ) ( 317-555-0193) email address ( info@dulomhome.com) website ( www.dulomhome.com ) and social media logos (Facebook- twitter- google plus )
3- company logo
4- licensed . insured . bonded

```html
<!DOCTYPE html>
<html lang="en">
<head>
<meta charset="UTF-8">
<title>Dulom Home Remodeling – Business Card</title>
<link rel="stylesheet" href="https://fonts.googleapis.com/css2?family=Open+Sans:wght@400;600;700;800&display=swap">
<style>
  :root {
    --backdrop-top: #2b2b2b;
    --backdrop-bottom: #040404;
    --card: #ffffff;
    --ink: #111111;
    --brand-dark: #3a3a3c;
    --brand-grey: #6d6e70;
    --brand-red: #c5232b;
    --social: #2a2a2a;
  }
  * { margin: 0; padding: 0; box-sizing: border-box; }
  html, body { width: 1200px; height: 900px; overflow: hidden; }
  body {
    position: relative;
    background: linear-gradient(180deg, var(--backdrop-top) 0%, #161616 55%, var(--backdrop-bottom) 100%);
    font-family: "Open Sans", Arial, sans-serif;
    color: var(--ink);
  }
  .card {
    position: absolute;
    top: 306px;
    width: 440px;
    height: 271px;
    background: var(--card);
    border-radius: 10px;
    box-shadow: 0 2px 6px rgba(0,0,0,.45);
  }
  .card--front { left: 149px; }
  .card--back { left: 608px; }

  .brand { position: absolute; display: flex; flex-direction: column; }
  .brand__row { display: flex; align-items: center; gap: 8px; }
  .brand__square { width: 9px; height: 9px; background: var(--brand-red); }
  .brand__name {
    font-weight: 800;
    color: var(--brand-dark);
    letter-spacing: 1px;
    line-height: 1;
  }
  .brand__tagline {
    color: var(--brand-grey);
    font-weight: 400;
    text-transform: uppercase;
    line-height: 1;
  }
  .card--front .brand { left: 26px; top: 28px; }
  .card--front .brand__name { font-size: 42px; }
  .card--front .brand__tagline { font-size: 12.5px; letter-spacing: 3.6px; margin: 6px 0 0 17px; }

  .card--back .brand { left: 87px; top: 92px; }
  .card--back .brand__name { font-size: 46px; }
  .card--back .brand__tagline { font-size: 14px; letter-spacing: 3.8px; margin: 6px 0 0 18px; }

  .person { position: absolute; left: 268px; top: 90px; }
  .person__name { color: var(--brand-red); font-weight: 600; font-size: 14.5px; line-height: 1.2; }
  .person__title { font-size: 12px; line-height: 1.5; }

  .contacts { position: absolute; left: 271px; top: 150px; list-style: none; }
  .contacts li { display: flex; align-items: center; gap: 6px; font-size: 12px; height: 18px; }
  .contacts svg { width: 9px; height: 9px; fill: var(--brand-red); flex: none; }

  .social { position: absolute; left: 271px; top: 234px; display: flex; gap: 7px; }
  .social span { width: 15px; height: 15px; border-radius: 50%; background: var(--social); }

  .credentials {
    position: absolute; left: 0; right: 0; top: 162px;
    display: flex; justify-content: center; align-items: center; gap: 8px;
    font-size: 17.5px; font-weight: 600; color: #222;
  }
  .credentials__dot { width: 8px; height: 8px; border-radius: 50%; background: var(--brand-red); }
</style>
</head>
<body>
  <section class="card card--front">
    <div class="brand">
      <div class="brand__row"><span class="brand__square"></span><span class="brand__name">DULOM</span></div>
      <span class="brand__tagline">Home Remodeling</span>
    </div>
    <div class="person">
      <p class="person__name">Karim Feltous</p>
      <p class="person__title">CEO / General Contractor</p>
    </div>
    <ul class="contacts">
      <li><svg viewBox="0 0 10 10"><path d="M2 .5l1.8 2-1 1.2c.6 1.3 1.5 2.2 2.6 2.7l1.1-1 2 1.7-1 1.9C4 8.8 1 5.8.4 1.6z"/></svg>1-888-DULOM-47</li>
      <li><svg viewBox="0 0 10 10"><path d="M2 .5l1.8 2-1 1.2c.6 1.3 1.5 2.2 2.6 2.7l1.1-1 2 1.7-1 1.9C4 8.8 1 5.8.4 1.6z"/></svg>317-555-0193</li>
      <li><svg viewBox="0 0 10 10"><path d="M.5 2h9v6h-9z M.5 2l4.5 3.5L9.5 2" fill="var(--brand-red)" stroke="#fff" stroke-width=".8"/></svg>info@dulomhome.com</li>
      <li><svg viewBox="0 0 10 10"><path d="M4 6l2-2M3.5 4.5L2 6a1.4 1.4 0 002 2l1.5-1.5M6.5 5.5L8 4a1.4 1.4 0 00-2-2L4.5 3.5" fill="none" stroke="var(--brand-red)" stroke-width="1.2" stroke-linecap="round"/></svg>www.dulomhome.com</li>
    </ul>
    <div class="social" role="img" aria-label="Social media links">
      <span></span><span></span><span></span>
    </div>
  </section>

  <section class="card card--back">
    <div class="brand">
      <div class="brand__row"><span class="brand__square"></span><span class="brand__name">DULOM</span></div>
      <span class="brand__tagline">Home Remodeling</span>
    </div>
    <p class="credentials">
      <span>Licensed</span><span class="credentials__dot"></span>
      <span>Insured</span><span class="credentials__dot"></span>
      <span>Bonded</span>
    </p>
  </section>
</body>
</html>
```